we can communicate on this, but i want to follow the approach we took on Pellew|Marsh & Quinlan but i feel the card front needs the black background and the platinum and gold logo. The back? I am open. we can use the same info from PM&Q. Velmont Arc is an enhanced equity investment fund - basically a very exclusive boutique hedge fund that uses only stock options. very advanced things. hope you are interested

Contact Information for Business Card

Dr. Lewis T. Brennick, CFA
Scientifique de fusée financière
701.555.0143
LTBquant47@mailvantor.com

4718 Willow Creek Bend W.
West Fargo, ND 58078

No web site

Colors

Designer to choose colors to be used in the design.

Requirements
Nice to have
• I tend to prefer the most visible applications of the logo to include logo and name, the logo version with a black background and the gold and platinum components separated by the black. I see this working well for a single side (logo and name - this is card front to me).
• I am fairly open to other treatments on the reverse side with the data. To me, it makes sense to have a different color rendition of the logo on the reverse and it may be a muted black tone on tone or an oversized portion that would have spot UV. Or, the reverse may play with colors and layout
Should not have
• Other colors = no no
• Decorative font

```html
<!DOCTYPE html>
<html lang="en">
<head>
<meta charset="utf-8">
<title>Velmont Arc – Business Card</title>
<link href="https://fonts.googleapis.com/css2?family=Montserrat:wght@700&family=Roboto:wght@400;700&display=swap" rel="stylesheet">
<style>
  :root {
    --backdrop: #3b3b3d;
    --card: #232325;
    --gold: #d4a82a;
    --white: #f4f4f4;
    --muted: #cfcfcf;
  }
  * { margin: 0; padding: 0; box-sizing: border-box; }
  html, body { width: 799px; height: 1200px; overflow: hidden; }
  body {
    background: var(--backdrop);
    font-family: "Roboto", sans-serif;
    position: relative;
  }
  .card {
    position: absolute;
    left: 80px;
    width: 640px;
    height: 366px;
    background: var(--card);
    border-radius: 4px;
  }
  .card--front { top: 100px; }
  .card--back { top: 700px; }

  .brand {
    position: absolute;
    display: flex;
    flex-direction: column;
    align-items: center;
  }
  .brand__mark {
    border-radius: 50%;
    background: var(--gold);
  }
  .brand__name {
    font-family: "Montserrat", sans-serif;
    font-weight: 700;
    color: var(--white);
    letter-spacing: 0.04em;
    text-transform: uppercase;
    white-space: nowrap;
  }
  .card--front .brand { left: 0; right: 0; top: 78px; }
  .card--front .brand__mark { width: 118px; height: 118px; margin-bottom: 22px; }
  .card--front .brand__name { font-size: 52px; line-height: 1; }

  .card--back .brand { left: 40px; width: 260px; top: 110px; }
  .card--back .brand__mark { width: 78px; height: 78px; margin-bottom: 14px; }
  .card--back .brand__name { font-size: 32px; line-height: 1; }

  .contact {
    position: absolute;
    left: 330px;
    top: 110px;
    color: var(--white);
  }
  .contact__name {
    font-weight: 700;
    font-size: 21px;
    color: var(--gold);
  }
  .contact__title {
    font-size: 15px;
    color: var(--muted);
    margin-top: 3px;
  }
  .contact__list {
    list-style: none;
    margin-top: 18px;
    font-size: 15px;
  }
  .contact__list li {
    display: flex;
    align-items: center;
    gap: 10px;
    margin-bottom: 6px;
  }
  .contact__list svg { width: 13px; height: 13px; fill: var(--gold); flex: none; }
  .contact__address {
    font-size: 15px;
    line-height: 1.35;
    margin-top: 6px;
  }
</style>
</head>
<body>

<section class="card card--front" aria-label="Card front">
  <div class="brand">
    <span class="brand__mark"></span>
    <span class="brand__name">Velmont Arc</span>
  </div>
</section>

<section class="card card--back" aria-label="Card back">
  <div class="brand">
    <span class="brand__mark"></span>
    <span class="brand__name">Velmont Arc</span>
  </div>

  <div class="contact">
    <p class="contact__name">Dr. Lewis T. Brennick, CFA</p>
    <p class="contact__title">Scientifique de fusée financière</p>
    <ul class="contact__list">
      <li>
        <svg viewBox="0 0 16 16" aria-hidden="true"><path d="M3 1h3l1.5 4-2 1.3a9 9 0 0 0 4.2 4.2L11 8.5l4 1.5v3a2 2 0 0 1-2 2A13 13 0 0 1 1 3a2 2 0 0 1 2-2z"/></svg>
        701.555.0143
      </li>
      <li>
        <svg viewBox="0 0 16 16" aria-hidden="true"><path d="M1 3h14v10H1z"/><path d="M1.5 3.5l6.5 5.5 6.5-5.5" fill="none" stroke="#232325" stroke-width="1.2"/></svg>
        LTBquant47@mailvantor.com
      </li>
    </ul>
    <p class="contact__address">4718 Willow Creek Bend W.,<br>West Fargo, ND 58078</p>
  </div>
</section>

</body>
</html>
```